Automotive spring company needs banner for website

Banner dimensions: 3840 x 880 pixels
Banner need to be consistent with our branding (logo, stationary, colors, fonts, message).
People images should show happiness and it is preferable those people are in or around a car unless it ties into one of the 3 quotes in the must haves below.
Use color blue #4885ed
and gold color #f7d105
Minimal, strong, clean, & tech

35-55 male and female

Auto Repair

• Clickable element for "Shop" or "Make an Appointment"
• "25 Years of Customer Satisfaction" or
• "Get it Done Right by Specialist" or
• "Peace of Mind National Warranty"
• Use our font, Eurostile and/or complimentary font paring

```html
<!DOCTYPE html>
<html lang="en">
<head>
<meta charset="UTF-8">
<title>Auto Spring Banner Options</title>
<link href="https://fonts.googleapis.com/css2?family=Michroma&family=Russo+One&display=swap" rel="stylesheet">
<style>
  :root {
    --navy: #020273;
    --brand-blue: #4885ed;
    --brand-gold: #f7d105;
    --label-grey: #d9dbe6;
    --ink: #111111;
    --white: #ffffff;
    --photo-light: #f4e6c9;
    --photo-mid: #e9d29a;
    --photo-warm: #d9b95e;
  }
  html, body {
    margin: 0;
    padding: 0;
    width: 1200px;
    height: 1200px;
    overflow: hidden;
    background: var(--navy);
  }
  .board {
    position: relative;
    width: 1200px;
    height: 1200px;
    background: var(--navy);
  }
  .option-label {
    position: absolute;
    left: 0;
    width: 1200px;
    text-align: center;
    font-family: "Russo One", sans-serif;
    font-size: 58px;
    line-height: 1;
    color: var(--label-grey);
  }
  .option-label--one { top: 173px; }
  .option-label--two { top: 953px; }

  .banner {
    position: absolute;
    left: 18px;
    width: 1164px;
    height: 267px;
    overflow: hidden;
  }
  .banner--one { top: 291px; }
  .banner--two { top: 610px; }

  .banner__art {
    position: absolute;
    inset: 0;
    width: 100%;
    height: 100%;
  }

  .headline {
    position: absolute;
    left: 824px;
    top: 22px;
    display: flex;
    align-items: flex-start;
  }
  .headline__number {
    font-family: "Russo One", sans-serif;
    font-size: 104px;
    line-height: 1;
    color: var(--brand-gold);
    letter-spacing: -2px;
  }
  .headline__words {
    margin-left: 8px;
    font-family: "Russo One", sans-serif;
    line-height: 0.85;
  }
  .headline__years {
    display: block;
    font-size: 38px;
    color: var(--brand-gold);
  }
  .headline__rest {
    display: block;
    font-size: 27px;
    color: var(--white);
    line-height: 0.84;
  }

  .tagline {
    position: absolute;
    left: 826px;
    width: 290px;
    text-align: center;
    font-family: "Michroma", sans-serif;
    margin: 0;
  }
  .tagline__lead {
    top: 137px;
    font-size: 15px;
    letter-spacing: 3.2px;
    color: var(--white);
  }
  .tagline__key {
    top: 166px;
    font-size: 21px;
    letter-spacing: 5px;
    color: var(--brand-gold);
  }

  .cta {
    position: absolute;
    left: 839px;
    top: 211px;
    width: 271px;
    height: 33px;
    background: var(--brand-gold);
    color: var(--ink);
    font-family: "Michroma", sans-serif;
    font-size: 12.5px;
    letter-spacing: 2.4px;
    text-decoration: none;
    display: flex;
    align-items: center;
    justify-content: center;
  }
</style>
</head>
<body>
<main class="board">
  <div class="option-label option-label--one">1</div>

  <section class="banner banner--one">
    <svg class="banner__art" viewBox="0 0 1164 267" preserveAspectRatio="none" aria-hidden="false">
      <defs>
        <linearGradient id="photoToneA" x1="0" y1="0" x2="0.3" y2="1">
          <stop offset="0" stop-color="#f6ead2"/>
          <stop offset="0.55" stop-color="#ecd9a8"/>
          <stop offset="1" stop-color="#b6a47a"/>
        </linearGradient>
      </defs>
      <rect x="0" y="0" width="1164" height="267" fill="var(--brand-blue)"/>
      <rect x="0" y="0" width="100" height="267" fill="var(--brand-blue)" role="img" aria-label="Coil spring pattern strip"/>
      <polygon points="100,0 792,0 688,267 100,267" fill="url(#photoToneA)" role="img" aria-label="Photo of a happy woman in a yellow shirt standing in a convertible car with arms outstretched"/>
      <polygon points="774,0 792,0 706,267 688,267" fill="var(--brand-gold)"/>
      <polygon points="792,0 1164,0 1164,267 706,267" fill="var(--brand-blue)"/>
    </svg>
    <div class="headline">
      <span class="headline__number">25</span>
      <span class="headline__words">
        <span class="headline__years">years</span>
        <span class="headline__rest">of customer</span>
        <span class="headline__rest">satisfaction</span>
      </span>
    </div>
    <p class="tagline tagline__lead">Get it Done Right by</p>
    <p class="tagline tagline__key">SPECIALIST</p>
    <a class="cta" href="#appointment">MAKE AN APPOINTMENT</a>
  </section>

  <section class="banner banner--two">
    <svg class="banner__art" viewBox="0 0 1164 267" preserveAspectRatio="none" aria-hidden="false">
      <defs>
        <linearGradient id="photoToneB" x1="0" y1="0" x2="0.3" y2="1">
          <stop offset="0" stop-color="#f6ead2"/>
          <stop offset="0.55" stop-color="#ecd9a8"/>
          <stop offset="1" stop-color="#b6a47a"/>
        </linearGradient>
      </defs>
      <rect x="0" y="0" width="1164" height="267" fill="var(--brand-blue)"/>
      <rect x="0" y="0" width="100" height="267" fill="var(--brand-blue)" role="img" aria-label="Coil spring pattern strip"/>
      <polygon points="100,0 792,0 688,267 100,267" fill="url(#photoToneB)" role="img" aria-label="Photo of a happy woman in a yellow shirt standing in a convertible car with arms outstretched"/>
      <polygon points="774,0 792,0 706,267 688,267" fill="var(--brand-gold)"/>
      <polygon points="792,0 1164,0 1164,267 706,267" fill="var(--brand-blue)"/>
    </svg>
    <div class="headline">
      <span class="headline__number">25</span>
      <span class="headline__words">
        <span class="headline__years">years</span>
        <span class="headline__rest">of customer</span>
        <span class="headline__rest">satisfaction</span>
      </span>
    </div>
    <p class="tagline tagline__lead">Get it Done Right by</p>
    <p class="tagline tagline__key">SPECIALIST</p>
    <a class="cta" href="#appointment">MAKE AN APPOINTMENT</a>
  </section>

  <div class="option-label option-label--two">2</div>
</main>
</body>
</html>
```